Business Card Design Project

I need a business card designed from scratch. I have an existing logo that I can upload in Illustrator for modification or redesign.

The Company is called Query Lanterns http://querylanterns.com.au and we provide Search Engine Optimization services to Australian businesses. The current logo signifies an increase in visitors, profits etc...

There are no restrictions as to the redesign - colours, style etc are all open to change.

Cards will be full colour and one sided printed at http://www.cardmoxel.com.au so check their requirements for file format and sizes etc.

I will expect all original files upon completion of project.

Target Market(s)

Any business with a web site looking to improve their search engine rankings

Industry/Entity Type

Business

Requirements
Must have
• I like modern, sleek designs. Clean, not fussy, uncluttered.

```html
<!DOCTYPE html>
<html lang="en">
<head>
<meta charset="utf-8">
<title>Query Lanterns – Business Card</title>
<link href="https://fonts.googleapis.com/css2?family=Open+Sans:wght@400;700;800&display=swap" rel="stylesheet">
<style>
  :root {
    --backdrop: #e9e6e2;
    --card: #ffffff;
    --brand-blue: #1f6db3;
    --brand-yellow: #f2c511;
    --ink: #4a4a4a;
    --ink-soft: #6b6b6b;
    --faint: #eef2f7;
  }
  html, body {
    margin: 0;
    width: 1200px;
    height: 460px;
    overflow: hidden;
    background: var(--backdrop);
    font-family: "Open Sans", Arial, sans-serif;
  }
  .stage {
    position: relative;
    width: 1200px;
    height: 460px;
  }
  .card {
    position: absolute;
    top: 88px;
    width: 540px;
    height: 306px;
    background: var(--card);
    border-radius: 16px;
    box-shadow: 0 3px 8px rgba(0,0,0,0.18);
    overflow: hidden;
  }
  .card--front { left: 36px; }
  .card--back { left: 613px; }

  .brand {
    position: absolute;
    display: flex;
    align-items: center;
    gap: 10px;
    color: var(--brand-blue);
    font-weight: 800;
    white-space: nowrap;
  }
  .brand__dot {
    border-radius: 50%;
    background: var(--brand-yellow);
    flex: none;
  }
  .card--front .brand {
    left: 36px;
    top: 40px;
    font-size: 34px;
    letter-spacing: -0.5px;
  }
  .card--front .brand__dot { width: 22px; height: 22px; }

  .faint-mark {
    position: absolute;
    right: 30px;
    top: 50px;
    width: 230px;
    height: 230px;
    border-radius: 50%;
    background: var(--faint);
  }

  .person {
    position: absolute;
    left: 26px;
    top: 142px;
    margin: 0;
    font-size: 16px;
    color: var(--brand-blue);
    font-weight: 700;
  }
  .person__title {
    font-weight: 400;
    font-size: 13px;
    color: var(--ink);
  }
  .address {
    position: absolute;
    left: 26px;
    top: 187px;
    margin: 0;
    font-size: 13px;
    line-height: 18px;
    color: var(--ink);
    font-style: normal;
  }
  .contacts {
    position: absolute;
    left: 26px;
    top: 240px;
    display: grid;
    grid-template-columns: auto auto;
    column-gap: 8px;
    row-gap: 1px;
    font-size: 13px;
    line-height: 18px;
    color: var(--ink);
  }
  .contact {
    display: flex;
    align-items: center;
    gap: 5px;
  }
  .contact svg { width: 10px; height: 10px; fill: var(--brand-blue); flex: none; }

  .back-url {
    position: absolute;
    left: 34px;
    top: 136px;
    font-size: 13px;
    color: var(--ink-soft);
  }
  .card--back .brand {
    left: 236px;
    top: 130px;
    font-size: 30px;
  }
  .card--back .brand__dot { width: 40px; height: 40px; }
</style>
</head>
<body>
<main class="stage">
  <section class="card card--front" aria-label="Card front">
    <div class="faint-mark" aria-hidden="true"></div>
    <div class="brand"><span class="brand__dot"></span>Query Lanterns</div>

    <p class="person">Your Name <span class="person__title">Title</span></p>

    <address class="address">00Floor Street, City Name<br>State Name, Contry Name</address>

    <div class="contacts">
      <span class="contact">
        <svg viewBox="0 0 10 10"><path d="M2 0.5 L3.6 2.6 L2.8 3.8 Q4 6 6.2 7.2 L7.4 6.4 L9.5 8 Q8.6 9.8 7 9.5 Q1.5 8 0.5 3 Q0.3 1.3 2 0.5Z"/></svg>
        098 765 4321
      </span>
      <span class="contact">
        <svg viewBox="0 0 10 10"><rect x="0" y="2" width="10" height="6.5" rx="1"/></svg>
        enquiry@querylanterns.com.au
      </span>
      <span class="contact">
        <svg viewBox="0 0 10 10"><rect x="2" y="0" width="6" height="10" rx="1"/><rect x="3" y="1.5" width="4" height="5" fill="#fff"/></svg>
        098 765 4321
      </span>
      <span class="contact">
        <svg viewBox="0 0 10 10"><circle cx="5" cy="5" r="4.5"/></svg>
        www.querylanterns.com.au
      </span>
    </div>
  </section>

  <section class="card card--back" aria-label="Card back">
    <span class="back-url">www.querylanterns.com.au</span>
    <div class="brand"><span class="brand__dot"></span>Query Lanterns</div>
  </section>
</main>
</body>
</html>
```